TK Homes - Stone Dorf Design

Looking for a double sides design, 1 side for my realestate and the other for home building. ( TK Homes on 1 side, Stone Dorf card on the other Side
Side 1 - Marek Tove ~ Vox Realty logo and Company ( the Property quarter )
Marek Tove
Marek@Marektove.example
IG - Marek_Bzq_Realtor
FB - marekt
Cell - 5558130467
3847 61 St Nw

Side 2
Marek Tove
5558130467
IG - Stonedorf_Bzq
Stonedorfdev@mailbox.example

Target Market(s)

Home buyers/ sellers

Industry/Entity Type

Home builders - Realestate

Contact Information for Business Card

Above

Requirements
Must have
• Black OR White background - my information -

```html
<!DOCTYPE html>
<html lang="en">
<head>
<meta charset="utf-8">
<title>Marek Tove – Business Cards</title>
<link href="https://fonts.googleapis.com/css2?family=Tinos:wght@400;700&display=swap" rel="stylesheet">
<style>
  :root {
    --page: #e9e6e2;
    --card: #000000;
    --edge: #c8453a;
    --blue: #1c74c4;
    --red: #d9493a;
    --white: #ffffff;
  }
  html, body {
    margin: 0;
    padding: 0;
    overflow: hidden;
  }
  body {
    width: 1200px;
    height: 780px;
    background: var(--page);
    display: flex;
    align-items: center;
    justify-content: center;
    gap: 80px;
    font-family: "Tinos", "Times New Roman", serif;
  }
  .card {
    position: relative;
    width: 400px;
    height: 680px;
    background: var(--card);
    border-radius: 28px;
    box-shadow: 0 0 0 2px var(--edge);
    box-sizing: border-box;
    color: var(--white);
    overflow: hidden;
  }
  .brand {
    position: absolute;
    top: 70px;
    left: 0;
    right: 0;
    text-align: center;
    color: var(--blue);
    font-weight: 400;
    letter-spacing: 3px;
    text-transform: uppercase;
  }
  .brand--realty { font-size: 38px; }
  .brand--build { font-size: 34px; line-height: 1.15; }
  .brand-mark {
    display: block;
    width: 16px;
    height: 16px;
    margin: 0 auto 14px;
    background: var(--red);
  }
  .identity {
    position: absolute;
    right: 16px;
  }
  .card--realty .identity { top: 390px; left: 110px; }
  .card--build .identity { top: 470px; left: 96px; }
  .name {
    margin: 0;
    font-size: 38px;
    font-weight: 700;
    line-height: 1;
  }
  .name .first { color: var(--blue); }
  .name .last { color: var(--red); }
  .role {
    margin: 4px 0 0 14px;
    font-size: 20px;
    font-weight: 700;
    line-height: 23px;
  }
  .address {
    margin: 22px 0 0 30px;
    font-size: 18px;
    line-height: 22px;
  }
  .contacts {
    list-style: none;
    margin: 16px 0 0 30px;
    padding: 0;
    font-size: 16px;
  }
  .card--build .contacts { margin-top: 12px; }
  .contacts li {
    display: flex;
    align-items: center;
    gap: 8px;
    height: 26px;
    line-height: 26px;
    white-space: nowrap;
  }
  .icon { width: 14px; height: 14px; flex: none; display: block; }
  .icon-dot { width: 13px; height: 13px; border-radius: 50%; background: var(--blue); flex: none; margin: 0 0.5px; }
  .icon-box { width: 13px; height: 13px; border: 2px solid var(--blue); border-radius: 3px; box-sizing: border-box; flex: none; margin: 0 0.5px; }
</style>
</head>
<body>

  <section class="card card--realty">
    <div class="brand brand--realty"><span class="brand-mark"></span>Marek Tove</div>
    <div class="identity">
      <h1 class="name"><span class="first">Marek</span> <span class="last">Tove</span></h1>
      <p class="role">Director</p>
      <p class="address">3847 61 St Nw</p>
      <ul class="contacts">
        <li>
          <svg class="icon" viewBox="0 0 16 16"><path fill="#1c74c4" d="M4 1l3 3-2 2c1 2 3 4 5 5l2-2 3 3-2 2C7 14 2 9 2 3z"/></svg>
          5558130467
        </li>
        <li><span class="icon-dot"></span>marekt</li>
        <li><span class="icon-box"></span>Marek_Bzq_Realtor</li>
        <li>
          <svg class="icon" viewBox="0 0 16 16"><rect x="1" y="3" width="14" height="10" fill="#1c74c4"/><path d="M1 3l7 6 7-6" fill="none" stroke="#000" stroke-width="1.2"/></svg>
          Marek@Marektove.example
        </li>
        <li>
          <svg class="icon" viewBox="0 0 16 16"><g fill="none" stroke="#1c74c4" stroke-width="1.4"><circle cx="8" cy="8" r="6.3"/><ellipse cx="8" cy="8" rx="2.8" ry="6.3"/><path d="M1.7 8h12.6"/></g></svg>
          www.marektove.example
        </li>
      </ul>
    </div>
  </section>

  <section class="card card--build">
    <div class="brand brand--build"><span class="brand-mark"></span>Stone Dorf<br>Developments</div>
    <div class="identity">
      <h1 class="name"><span class="first">Marek</span> <span class="last">Tove</span></h1>
      <p class="role">Director</p>
      <ul class="contacts">
        <li>
          <svg class="icon" viewBox="0 0 16 16"><path fill="#1c74c4" d="M4 1l3 3-2 2c1 2 3 4 5 5l2-2 3 3-2 2C7 14 2 9 2 3z"/></svg>
          5558130467
        </li>
        <li><span class="icon-box"></span>Stonedorf_Bzq</li>
        <li>
          <svg class="icon" viewBox="0 0 16 16"><rect x="1" y="3" width="14" height="10" fill="#1c74c4"/><path d="M1 3l7 6 7-6" fill="none" stroke="#000" stroke-width="1.2"/></svg>
          Stonedorfdev@mailbox.example
        </li>
      </ul>
    </div>
  </section>

</body>
</html>
```